Commercial Loan Originator Business Card (CHANGE COLORS SCHEME)

CHANGE COLOR SCHEME - SAME DESIGN

Name Marlene Agate
Title Commercial Loan Originator
Office (800) 417-2906 x68
Direct (240) 615-2043
Email freshgreens4life@quillbox.example

Name Dale Morrow
Office (800) 417-2906 x70
Direct (410) 392-5184
Email d.morthehomeguy@quillbox.example

Name Leonard Vasko
Office (800) 417-2906 x71
Direct (215) 463-0712
Email l.vasko41@quillbox.example

Name Gwen Halsey
Office (800) 417-2906 x
Direct (202) 548-1370
Email ghalsey63@quillbox.example

Name Mirna Ashby
Office (800) 417-2906 x72
Direct (240) 871-4526
Email tristatehomelending@quillbox.example

```html
<!DOCTYPE html>
<html lang="en">
<head>
<meta charset="utf-8">
<title>Commercial Loan Originator Business Cards</title>
<link rel="stylesheet" href="https://fonts.googleapis.com/css2?family=Poppins:wght@300;400;500&display=swap">
<style>
  :root {
    --board: #151515;
    --board-glow: #2a2a2a;
    --white: #ffffff;
    --ink: #333333;
    --blue: #234ea0;
    --plum: #a8388f;
    --copper: #b5693a;
    --pine: #3e5a51;
    --raspberry: #bc1e5e;
  }
  * { box-sizing: border-box; margin: 0; padding: 0; }
  html, body { width: 1189px; height: 1200px; overflow: hidden; }
  body {
    position: relative;
    background: radial-gradient(ellipse at 50% 45%, var(--board-glow), var(--board) 75%);
    font-family: "Poppins", sans-serif;
  }
  .index {
    position: absolute;
    color: var(--white);
    font-size: 23px;
    font-weight: 300;
    line-height: 1;
  }
  .card {
    position: absolute;
    width: 500px;
    height: 286px;
    box-shadow: 0 6px 18px rgba(0,0,0,.55);
    background: linear-gradient(to bottom,
      var(--accent) 0 20px,
      var(--white) 20px 149px,
      var(--accent) 149px 253px,
      var(--white) 253px 286px);
  }
  .portrait {
    position: absolute;
    left: 54px;
    top: 58px;
    width: 166px;
    height: 166px;
    border-radius: 50%;
    border: 3px solid var(--accent);
    background: var(--photo);
  }
  .name {
    position: absolute;
    left: 272px;
    top: 70px;
    color: var(--accent);
    font-size: 21px;
    font-weight: 500;
    line-height: 1.2;
    white-space: nowrap;
  }
  .title {
    position: absolute;
    left: 272px;
    top: 95px;
    color: var(--ink);
    font-size: 12.5px;
    font-weight: 400;
    white-space: nowrap;
  }
  .rule {
    position: absolute;
    left: 272px;
    top: 124px;
    width: 52px;
    height: 2px;
    background: var(--accent);
  }
  .contacts {
    position: absolute;
    left: 276px;
    top: 163px;
    list-style: none;
    color: var(--white);
    font-weight: 300;
    font-size: 12.5px;
    line-height: 15.5px;
  }
  .contacts li { display: flex; align-items: center; white-space: nowrap; }
  .contacts svg { width: 9px; height: 9px; margin-right: 4px; flex: none; fill: var(--white); }
  .contacts .email { font-size: 11px; }
  .contacts .email.long { font-size: 10px; }
</style>
</head>
<body>

<svg width="0" height="0" style="position:absolute" aria-hidden="true">
  <defs>
    <symbol id="icon-phone" viewBox="0 0 10 10"><path d="M1 3.5C1 2 2.5 1 5 1s4 1 4 2.5L7.5 4 7 3H3L2.5 4zM2.5 4.5h5L8.5 9h-7z"/></symbol>
    <symbol id="icon-mobile" viewBox="0 0 10 10"><path d="M2.5 1h5v8h-5zM3.5 2v6h3V2z" fill-rule="evenodd"/></symbol>
    <symbol id="icon-mail" viewBox="0 0 10 10"><path d="M1 2.5h8v5H1zM1.8 3l3.2 2.5L8.2 3z" fill-rule="evenodd"/></symbol>
  </defs>
</svg>

<span class="index" style="left:33px;top:250px">1</span>
<span class="index" style="left:30px;top:583px">2</span>
<span class="index" style="left:30px;top:921px">3</span>
<span class="index" style="left:1146px;top:259px">4</span>
<span class="index" style="left:1146px;top:592px">5</span>

<article class="card" style="--accent:var(--blue);--photo:radial-gradient(circle at 50% 40%,#6b4a3a,#3a3f52 60%,#8aa2b8);left:73px;top:126px">
  <div class="portrait" role="img" aria-label="Portrait photo of Leonard Vasko"></div>
  <h2 class="name">Leonard Vasko</h2>
  <p class="title">Commercial Loan Originator</p>
  <div class="rule"></div>
  <ul class="contacts">
    <li><svg><use href="#icon-phone"/></svg>(800) 417-2906 x71</li>
    <li><svg><use href="#icon-mobile"/></svg>(215) 463-0712</li>
    <li class="email"><svg><use href="#icon-mail"/></svg>l.vasko41@quillbox.example</li>
  </ul>
</article>

<article class="card" style="--accent:var(--plum);--photo:radial-gradient(circle at 50% 45%,#7a5245,#5a4a48 55%,#8a5a50);left:604px;top:126px">
  <div class="portrait" role="img" aria-label="Portrait photo of Gwen Halsey"></div>
  <h2 class="name">Gwen Halsey</h2>
  <p class="title">Commercial Loan Originator</p>
  <div class="rule"></div>
  <ul class="contacts">
    <li><svg><use href="#icon-phone"/></svg>(800) 417-2906 x</li>
    <li><svg><use href="#icon-mobile"/></svg>(202) 548-1370</li>
    <li class="email"><svg><use href="#icon-mail"/></svg>ghalsey63@quillbox.example</li>
  </ul>
</article>

<article class="card" style="--accent:var(--copper);--photo:radial-gradient(circle at 50% 45%,#7a4e38,#5e3f33 55%,#9a8070);left:73px;top:459px">
  <div class="portrait" role="img" aria-label="Portrait photo of Mirna Ashby"></div>
  <h2 class="name">Mirna Ashby</h2>
  <p class="title">Commercial Loan Originator</p>
  <div class="rule"></div>
  <ul class="contacts">
    <li><svg><use href="#icon-phone"/></svg>(800) 417-2906 x72</li>
    <li><svg><use href="#icon-mobile"/></svg>(240) 871-4526</li>
    <li class="email long"><svg><use href="#icon-mail"/></svg>tristatehomelending@quillbox.example</li>
  </ul>
</article>

<article class="card" style="--accent:var(--pine);--photo:radial-gradient(circle at 50% 40%,#5a4034,#3a3634 55%,#b8bcc0);left:604px;top:456px">
  <div class="portrait" role="img" aria-label="Portrait photo of Dale Morrow"></div>
  <h2 class="name">Dale Morrow</h2>
  <p class="title">Commercial Loan Originator</p>
  <div class="rule"></div>
  <ul class="contacts">
    <li><svg><use href="#icon-phone"/></svg>(800) 417-2906 x70</li>
    <li><svg><use href="#icon-mobile"/></svg>(410) 392-5184</li>
    <li class="email"><svg><use href="#icon-mail"/></svg>d.morthehomeguy@quillbox.example</li>
  </ul>
</article>

<article class="card" style="--accent:var(--raspberry);--photo:radial-gradient(circle at 50% 40%,#8a5a48,#b07a80 55%,#eeeeee);left:73px;top:789px">
  <div class="portrait" role="img" aria-label="Portrait photo of Marlene Agate"></div>
  <h2 class="name">Marlene Agate</h2>
  <p class="title">Commercial Loan Originator</p>
  <div class="rule"></div>
  <ul class="contacts">
    <li><svg><use href="#icon-phone"/></svg>(800) 417-2906 x68</li>
    <li><svg><use href="#icon-mobile"/></svg>(240) 615-2043</li>
    <li class="email"><svg><use href="#icon-mail"/></svg>freshgreens4life@quillbox.example</li>
  </ul>
</article>

</body>
</html>
```